Website for 3d printing & other services

Hi, i'm after a website to sell my 3d printed automotive parts as well as sell my 3d printing services & other services.

There's a few things i need the website to have:

- Automatic 3d print quoting based on the file the client uploads to the website.
- Shop function where i can sell my custom automotive parts
- 3D printing technologies offered are SLA & FDM
- My business can offer 3d printing, 3d scanning, 3d cad design, cnc machining, steel fabrication, drafting services.

The color design is to suit my logo which is Black, orange & white.

Target Market(s)

3d printing, automotive, fabrication

Industry/Entity Type

General manufacturing & Custom automotive parts

Coding

Coded - Design and coding required

Number of Pages Required

5+ page

Requirements
Must have
• Automatic 3d print quoting. Shop for my printed parts.

```html
<!DOCTYPE html>
<html lang="en">
<head>
<meta charset="utf-8">
<title>Vantor Draft &amp; Design</title>
<link href="https://fonts.googleapis.com/css2?family=Krona+One&family=Arimo:wght@400;700&display=swap" rel="stylesheet">
<style>
:root{
  --orange:#ff6a00;
  --black:#000;
  --white:#fff;
  --ink:#111;
  --field:#e6e6e6;
  --hero:#d9d9d9;
}
*{margin:0;padding:0;box-sizing:border-box}
html,body{width:1200px;height:3936px;overflow:hidden;background:var(--white)}
body{position:relative;font-family:"Arimo",Arial,sans-serif;color:var(--ink)}
.display{font-family:"Krona One","Arial Black",sans-serif}
.abs{position:absolute}
.accent{color:var(--orange)}
section,header,footer{position:absolute;left:0;width:1200px}

/* header */
.site-header{top:0;height:107px;background:var(--black)}
.brand{position:absolute;display:flex;align-items:center;gap:8px;font-family:"Krona One",sans-serif;color:var(--orange);font-size:13px;line-height:17px}
.brand-dot{width:14px;height:14px;border-radius:50%;background:var(--orange)}
.nav{position:absolute;display:flex;font-family:"Krona One",sans-serif;font-size:12px;color:var(--white);letter-spacing:.3px}

/* buttons */
.btn{position:absolute;display:flex;align-items:center;border-radius:40px;background:var(--orange);color:var(--white);font-family:"Krona One",sans-serif;overflow:hidden}
.btn-label{flex:1;padding-left:22px}
.btn-arrow{background:var(--black);height:100%;border-radius:40px;display:flex;align-items:center;justify-content:center}

/* hero */
.hero{top:107px;height:515px;background:radial-gradient(circle at 30% 40%,#ececec,#c9c9c9 70%,#bdbdbd)}
.hero-media{position:absolute;left:690px;top:0;width:420px;height:515px;background:linear-gradient(90deg,#8a8a8a,#2a2a2a 40%,#555 60%,#b0b0b0);border-radius:0 0 40px 40px;opacity:.9}
.section-title{position:absolute;left:0;width:1200px;text-align:center;font-family:"Krona One",sans-serif;font-size:28px}
.body-copy{position:absolute;font-size:15px;line-height:34.3px;color:var(--ink)}

.photo{position:absolute;border-radius:14px}

/* printing */
.print-band{top:1386px;height:514px;background:var(--black)}
.tech-card{position:absolute;top:146px;width:477px;height:288px;background:var(--white);border-radius:20px}
.tech-card .photo{left:10px;top:13px;width:228px;height:263px;border-radius:16px}
.tech-name{position:absolute;left:263px;top:32px;font-family:"Krona One",sans-serif;font-size:21px;color:var(--orange)}
.tech-copy{position:absolute;left:263px;top:70px;width:200px;font-size:15px;line-height:32px}

/* services */
.services{top:1900px;height:633px}
.service{position:absolute;top:185px;width:233px}
.service .photo{position:relative;width:233px;height:313px;border-radius:10px}
.service-name{margin-top:26px;text-align:center;font-family:"Krona One",sans-serif;font-size:18px;color:var(--orange)}
.slider-arrow{position:absolute;top:318px;width:46px;height:46px;border-radius:50%;background:var(--orange);display:flex;align-items:center;justify-content:center}

/* testimonials */
.testimonials{top:2533px;height:515px;background:var(--black);color:var(--white)}
.quote-text{position:absolute;left:265px;width:670px;top:269px;font-size:15px;line-height:34.5px;text-align:justify;text-align-last:center}

/* quote */
.quote{top:3048px;height:535px}
.field{position:absolute;background:var(--field);font-family:"Krona One",sans-serif;font-size:12px;color:#222;padding:27px 0 0 25px}

/* footer */
.site-footer{top:3583px;height:353px;background:var(--black);color:var(--white)}
.social{position:absolute;top:224px;width:38px;height:38px;border-radius:50%;background:var(--orange)}
</style>
</head>
<body>

<header class="site-header">
  <div class="brand" style="left:100px;top:34px"><span class="brand-dot"></span><span>VANTOR<br>DRAFT &amp; DESIGN</span></div>
  <nav class="nav" style="top:46px;left:298px">
    <span>ABOUT US</span><span style="margin-left:52px">SERVICES</span><span style="margin-left:52px">CUSTOM AUTOMOTIVE PARTS</span><span style="margin-left:52px">3D PRINTING TECHNOLOGIES</span>
  </nav>
</header>

<section class="hero">
  <div class="hero-media" role="img" aria-label="CNC milling spindle with end mill"></div>
  <div class="abs display accent" style="left:111px;top:102px;font-size:23px">WELCOME TO</div>
  <h1 class="abs display" style="left:111px;top:148px;font-size:34px;font-weight:400">VANTOR DRAFT AND DESIGN</h1>
  <p class="body-copy" style="left:111px;top:213px;width:580px">Sed ut perspiciatis unde omnis iste natus error sit voluptatem accusantium doloremque laudantium, totam rem aperiam, eaque ipsa quae ab illo inventore veritatis et quasi architecto beatae vitae dicta sunt explicabo.</p>
  <div class="btn" style="left:111px;top:350px;width:234px;height:59px;font-size:16px"><span class="btn-label">GET STARTED</span><span class="btn-arrow" style="width:58px"><svg width="28" height="14" viewBox="0 0 28 14"><path d="M1 7h25M20 1l6 6-6 6" stroke="#fff" stroke-width="2" fill="none"/></svg></span></div>
</section>

<section class="parts" style="top:622px;height:764px">
  <h2 class="section-title" style="top:84px;font-weight:400">OUR <span class="accent">CUSTOM AUTOMOTIVE</span> PARTS</h2>
  <div class="photo" role="img" aria-label="Close-up of machined gear parts" style="left:222px;top:186px;width:305px;height:364px;background:linear-gradient(135deg,#eee,#8d8d8d 50%,#d0d0d0)"></div>
  <div class="photo" role="img" aria-label="Engineer reviewing 3D CAD model on monitor" style="left:113px;top:318px;width:303px;height:360px;border:4px solid #fff;background:linear-gradient(160deg,#3c4450,#1b2028 60%,#4a5562)"></div>
  <p class="body-copy" style="left:601px;top:234px;width:490px">Sed ut perspiciatis unde omnis iste natus error sit voluptatem accusantium doloremque laudantium, totam rem aperiam, eaque ipsa quae ab illo inventore veritatis et quasi architecto beatae vitae dicta sunt explicabo. Lorem ipsum dolor sit amet, consectetur adipiscing elit, sed do eiusmod tempor incididunt ut labore et dolore magna aliqua. Ut enim ad minim veniam, quis nostrud exercitation ullamco laboris nisi ut aliquip ex ea commodo consequat.</p>
  <div class="btn" style="left:601px;top:551px;width:234px;height:58px;font-size:16px"><span class="btn-label" style="padding-left:32px">SHOP NOW</span><span class="btn-arrow" style="width:58px"><svg width="28" height="14" viewBox="0 0 28 14"><path d="M1 7h25M20 1l6 6-6 6" stroke="#fff" stroke-width="2" fill="none"/></svg></span></div>
</section>

<section class="print-band">
  <h2 class="section-title" style="top:60px;color:#fff;font-weight:400">3D PRINTING <span class="accent">TECHNOLOGIES</span></h2>
  <article class="tech-card" style="left:108px">
    <div class="photo" role="img" aria-label="SLA resin 3D printer" style="background:linear-gradient(180deg,#555,#1a1a1a 60%,#333)"></div>
    <h3 class="tech-name" style="font-weight:400">SLA</h3>
    <p class="tech-copy">Sed ut perspiciatis unde omnis iste natus error sit voluptatem accusantium doloremque laudantium,</p>
    <div class="btn" style="left:263px;top:216px;width:151px;height:36px;font-size:10px"><span class="btn-label" style="padding-left:17px">LEARN MORE</span><span class="btn-arrow" style="width:36px"><svg width="18" height="10" viewBox="0 0 18 10"><path d="M1 5h15M12 1l4 4-4 4" stroke="#fff" stroke-width="1.6" fill="none"/></svg></span></div>
  </article>
  <article class="tech-card" style="left:614px">
    <div class="photo" role="img" aria-label="FDM 3D printer printing a black vase" style="background:linear-gradient(180deg,#cfd6de,#9aa5b0 55%,#2a2a2a)"></div>
    <h3 class="tech-name" style="font-weight:400">FDM</h3>
    <p class="tech-copy">Sed ut perspiciatis unde omnis iste natus error sit voluptatem accusantium doloremque laudantium,</p>
    <div class="btn" style="left:263px;top:216px;width:151px;height:36px;font-size:10px"><span class="btn-label" style="padding-left:17px">LEARN MORE</span><span class="btn-arrow" style="width:36px"><svg width="18" height="10" viewBox="0 0 18 10"><path d="M1 5h15M12 1l4 4-4 4" stroke="#fff" stroke-width="1.6" fill="none"/></svg></span></div>
  </article>
</section>

<section class="services">
  <h2 class="section-title" style="top:84px;font-weight:400">OUR <span class="accent">SERVICES</span></h2>
  <div class="slider-arrow" style="left:31px"><svg width="20" height="12" viewBox="0 0 20 12"><path d="M19 6H2M7 1L2 6l5 5" stroke="#fff" stroke-width="1.8" fill="none"/></svg></div>
  <div class="slider-arrow" style="left:1121px"><svg width="20" height="12" viewBox="0 0 20 12"><path d="M1 6h17M13 1l5 5-5 5" stroke="#fff" stroke-width="1.8" fill="none"/></svg></div>
  <div class="service" style="left:110px"><div class="photo" role="img" aria-label="3D printer producing an orange gear" style="background:linear-gradient(160deg,#c0392b,#1b1b1b 55%,#e8551c)"></div><div class="service-name">3D PRINTING</div></div>
  <div class="service" style="left:358px"><div class="photo" role="img" aria-label="Handheld 3D scanner scanning a part" style="background:linear-gradient(160deg,#d9dde6,#7a5cff 55%,#eef0f5)"></div><div class="service-name">3D SCANNING</div></div>
  <div class="service" style="left:607px"><div class="photo" role="img" aria-label="CNC machine cutting a metal block" style="background:linear-gradient(180deg,#f0f0f0,#8c8c8c 60%,#3a3a3a)"></div><div class="service-name">CNC MACHINING</div></div>
  <div class="service" style="left:854px"><div class="photo" role="img" aria-label="Stacked steel tubes and profiles" style="background:linear-gradient(135deg,#e4e8ec,#7d858c 50%,#c9ced3)"></div><div class="service-name">STEEL FABRICATION</div></div>
</section>

<section class="testimonials">
  <h2 class="section-title accent" style="top:50px;font-weight:400">TESTIMONIALS</h2>
  <div class="abs" role="img" aria-label="Customer portrait" style="left:539px;top:120px;width:122px;height:122px;border-radius:50%;background:linear-gradient(180deg,#eee,#cfcfcf)"></div>
  <p class="quote-text">At vero eos et accusamus et iusto odio dignissimos ducimus qui blanditiis praesentium voluptatum deleniti atque corrupti quos dolores et quas molestias excepturi sint occaecati cupiditate non provident, similique sunt in culpa qui officia deserunt mollitia animi, id est</p>
  <div class="abs display" style="left:0;width:1200px;top:408px;text-align:center;font-size:15px"><span class="accent" style="font-size:18px">LOREM LIPSUM -</span> GENERAL MANAGER</div>
  <svg class="abs" style="left:560px;top:2450px;top:452px" width="82" height="12" viewBox="0 0 82 12"><circle cx="8" cy="6" r="4" fill="#fff"/><rect x="28" y="5" width="20" height="3" fill="#fff"/><rect x="58" y="5" width="20" height="3" fill="#fff"/></svg>
</section>

<section class="quote">
  <div class="abs" role="img" aria-label="CNC lathe cutting metal with sparks" style="left:0;top:0;width:581px;height:535px;background:linear-gradient(150deg,#1a2230,#56606c 45%,#12161c)"></div>
  <h2 class="abs display" style="left:581px;width:619px;top:48px;text-align:center;font-size:28px;font-weight:400">GET A <span class="accent">QUOTE</span></h2>
  <div class="field" style="left:640px;top:132px;width:240px;height:64px">FIRST NAME</div>
  <div class="field" style="left:891px;top:132px;width:240px;height:64px">LAST NAME</div>
  <div class="field" style="left:640px;top:210px;width:240px;height:64px">EMAIL ADDRESS</div>
  <div class="field" style="left:891px;top:210px;width:240px;height:64px">PHONE NUMBER</div>
  <div class="field" style="left:640px;top:288px;width:489px;height:118px;padding-top:22px">MESSAGE</div>
  <div class="btn" style="left:788px;top:437px;width:192px;height:47px;font-size:13px"><span class="btn-label" style="padding-left:22px">SUBMIT NOW</span><span class="btn-arrow" style="width:47px"><svg width="22" height="12" viewBox="0 0 22 12"><path d="M1 6h19M15 1l5 5-5 5" stroke="#fff" stroke-width="1.8" fill="none"/></svg></span></div>
</section>

<footer class="site-footer">
  <div class="brand" style="left:540px;top:48px"><span class="brand-dot"></span><span>VANTOR<br>DRAFT &amp; DESIGN</span></div>
  <nav class="nav" style="top:168px;left:200px;width:800px;justify-content:center">
    <span>ABOUT US</span><span style="margin-left:52px">SERVICES</span><span style="margin-left:52px">CUSTOM AUTOMOTIVE PARTS</span><span style="margin-left:52px">3D PRINTING TECHNOLOGIES</span>
  </nav>
  <span class="social" style="left:552px" aria-label="Social profile"></span>
  <span class="social" style="left:608px" aria-label="Social profile"></span>
  <p class="abs" style="left:0;width:1200px;top:294px;text-align:center;font-size:15px">@2023 COPYRIGHTS. VANTOR DRAFT &amp; DESIGN. ALL RIGHTS RESERVED.</p>
</footer>

</body>
</html>
```